NZ First of it's kind solutions directory and marketplace for busy Mums needs a business card design

We need a business card design for our new nationwide business in NZ (long term plans to go global). We provide solutions to the everyday challenges that busy Mums face by connecting them with quality communities and suppliers of carefully selected, relevant products and services. We sell direct via our online marketplace. The final design should communicate our values of inclusivity, quality and smart solutions. Colours should incorporate our logo colour palette of #477077 and #6ba8b2. Our website is at https://www.brightnestmums.example

Target Market(s)

busy Mums, Age 28 – 50, female, income over $100K, location main centres NZ primarily but NZ wide. Is likely juggling work or career with a young family. Probably had hobbies which have fallen by the wayside.
-Wants to succeed in her chosen career without compromising on family life
-to successfully juggle her career without feeling like she is compromising her children
- Is time poor, something always has to give and it’s generally her health (she’ll stay up late, get stressed)
- probably ex corporate or professional career. Has discretional income

Industry/Entity Type

Business

Contact Information for Business Card

Lena Forbisher, Founder, BrightNestMums.example (Strapline Tap; Gather; Sorted), 47 Kowhai Terrace, Ellerslie, Auckland 1051, New Zealand. Mob: 021 483 517 Ph: +64 (0)9 571 4860

Font styles to use
Other font styles liked:
• Raleway, and/or Architects Daughter

Colors
00a990
33b8a4
86cfc6
cfeae6

Requirements
Must have
• the above details, streamline. the logo and colours associated with those logos
Should not have
• foil or metallic colours

```html
<!DOCTYPE html>
<html lang="en">
<head>
<meta charset="utf-8">
<title>BrightNestMums – Business Card</title>
<link href="https://fonts.googleapis.com/css2?family=Nunito:ital,wght@0,800;1,400&family=Roboto+Condensed:wght@400&family=Raleway:wght@500&display=swap" rel="stylesheet">
<style>
  :root {
    --brand-dark: #477077;
    --brand-deep: #3b5d64;
    --brand-light: #6ba8b2;
    --ink: #2f4a50;
    --card: #f7f7f7;
    --page: #e6e6e6;
    --white: #ffffff;
  }
  * { box-sizing: border-box; margin: 0; padding: 0; }
  html, body {
    width: 1200px; height: 576px; overflow: hidden;
    background: var(--page);
  }
  .canvas { position: relative; width: 1200px; height: 576px; }

  .card {
    position: absolute; top: 138px;
    width: 484px; height: 294px;
    background: var(--card);
    border-radius: 14px;
    overflow: hidden;
  }
  .card--front { left: 82px; }
  .card--back { left: 634px; }

  /* Front */
  .front-mark {
    position: absolute; left: 50%; top: 62px;
    width: 46px; height: 46px; margin-left: -23px;
    border-radius: 50%;
    background: var(--brand-dark);
  }
  .wordmark {
    font-family: "Nunito", sans-serif;
    font-weight: 800;
    color: var(--brand-deep);
    letter-spacing: -0.5px;
    white-space: nowrap;
  }
  .front-wordmark {
    position: absolute; left: 0; right: 0; top: 122px;
    text-align: center; font-size: 34px; line-height: 1;
  }
  .strapline {
    position: absolute; left: 0; right: 0; top: 170px;
    text-align: center;
    font-family: "Raleway", sans-serif; font-weight: 500;
    font-size: 11px; letter-spacing: 4px;
    color: var(--ink);
  }
  .strapline .divider { color: var(--brand-light); margin: 0 6px; }

  /* Back */
  .back-mark {
    position: absolute; left: 30px; top: 52px;
    width: 38px; height: 38px; border-radius: 50%;
    background: var(--brand-dark);
  }
  .back-wordmark {
    position: absolute; left: 84px; top: 52px;
    font-size: 32px; line-height: 38px;
  }
  .person { position: absolute; left: 30px; top: 139px; }
  .person__name {
    font-family: "Nunito", sans-serif; font-weight: 800;
    font-size: 18px; color: var(--brand-deep); line-height: 1.1;
  }
  .person__role {
    font-family: "Nunito", sans-serif; font-style: italic; font-weight: 400;
    font-size: 11px; color: var(--ink); margin-top: 2px;
  }
  .wave { position: absolute; left: 0; top: 0; width: 484px; height: 294px; }

  .contact {
    position: absolute; right: 20px; top: 186px;
    list-style: none;
    font-family: "Roboto Condensed", sans-serif;
    font-size: 11.5px; color: var(--white);
    text-align: right;
  }
  .contact li {
    display: flex; justify-content: flex-end; align-items: center;
    height: 18.5px; gap: 9px;
  }
  .contact svg { width: 11px; height: 11px; flex: none; }
</style>
</head>
<body>
<main class="canvas">

  <section class="card card--front" aria-label="Card front">
    <div class="front-mark"></div>
    <div class="wordmark front-wordmark">BrightNestMums</div>
    <div class="strapline">TAP<span class="divider">|</span>GATHER<span class="divider">|</span>SORTED</div>
  </section>

  <section class="card card--back" aria-label="Card back">
    <div class="back-mark"></div>
    <div class="wordmark back-wordmark">BrightNestMums</div>

    <div class="person">
      <div class="person__name">Lena Forbisher</div>
      <div class="person__role">Founder</div>
    </div>

    <svg class="wave" viewBox="0 0 484 294" aria-hidden="true">
      <path fill="var(--brand-light)" d="M0,198 C70,228 190,236 292,188 C372,150 432,138 484,140 L484,154 C428,152 378,168 306,206 C206,256 88,246 0,216 Z"/>
      <path fill="var(--brand-light)" d="M40,228 C120,248 210,246 270,226 C200,252 110,250 40,228 Z"/>
      <path fill="var(--brand-dark)" d="M0,238 C110,274 240,258 322,212 C392,174 440,164 484,168 L484,294 L0,294 Z"/>
    </svg>

    <ul class="contact">
      <li>021 483 517
        <svg viewBox="0 0 12 12"><rect x="3" y="0.5" width="6" height="11" rx="1" fill="none" stroke="#fff" stroke-width="1.2"/><circle cx="6" cy="9.5" r="0.7" fill="#fff"/></svg>
      </li>
      <li>+64 (0)9 571 4860
        <svg viewBox="0 0 12 12"><path fill="#fff" d="M1,4 C1,2 3,1.5 6,1.5 C9,1.5 11,2 11,4 L9,4.5 L8.5,3.5 L3.5,3.5 L3,4.5 Z M3,5.5 L9,5.5 L10.5,10.5 L1.5,10.5 Z"/></svg>
      </li>
      <li>www.BrightNestMums.example
        <svg viewBox="0 0 12 12"><circle cx="6" cy="6" r="5" fill="none" stroke="#fff" stroke-width="1.1"/><path d="M1,6 H11 M6,1 C3,4 3,8 6,11 M6,1 C9,4 9,8 6,11" fill="none" stroke="#fff" stroke-width="0.9"/></svg>
      </li>
      <li>lena@brightnestmums.example
        <svg viewBox="0 0 12 12"><rect x="0.5" y="2.5" width="11" height="7.5" fill="#fff"/><path d="M0.5,2.5 L6,7 L11.5,2.5" fill="none" stroke="var(--brand-dark)" stroke-width="1"/></svg>
      </li>
      <li>47 Kowhai Terrace, Ellerslie, Auckland 1051, New Zealand
        <svg viewBox="0 0 12 12"><path fill="#fff" d="M6,0.5 C3.6,0.5 2,2.2 2,4.4 C2,7.2 6,11.5 6,11.5 C6,11.5 10,7.2 10,4.4 C10,2.2 8.4,0.5 6,0.5 Z"/><circle cx="6" cy="4.4" r="1.4" fill="var(--brand-dark)"/></svg>
      </li>
    </ul>
  </section>

</main>
</body>
</html>
```